Mobile Fitness snd Therapy Business Card Design

I need a business card designed for my mobile fitness and therapy business.

Please view the images that I have uploaded. I like the simplicity of the design that I have attached. I adapted it with my information

Target Market(s)

Those seeking personal training, injury rehabilitation or massage therapy.

Industry/Entity Type

Business

Contact Information for Business Card

Derek Fulham - MSc, CAT(C), RMT, CSCS, Pn2
e-mail: derek@vantrelo.com
website: www.vantrelo.com
instagram: @derek_fulham

Font styles to use
Sans Serif

Colors
3176b5
0355a3

Requirements
Must have
• "Contact us to receive a FREE assessment"
• Services offered:
• Personal Training
• Golf Fitness
• Injury Rehab
• Massage Therapy
• Yoga
Nice to have
• Consistent colours with brand
• - Dark Blue: #232837
• - Blue: #5096f0
• Consistent look/feel with the website: www.vantrelo.com

```html
<!DOCTYPE html>
<html lang="en">
<head>
<meta charset="utf-8">
<title>Vantrelo Business Card</title>
<link rel="stylesheet" href="https://fonts.googleapis.com/css2?family=Arimo:wght@400;700&display=swap">
<style>
  :root {
    --page-bg: #eef0f3;
    --card-white: #ffffff;
    --brand-dark: #232837;
    --brand-blue: #5096f0;
    --blue-deep: #2456c8;
    --grad-start: #2a5bd4;
    --grad-end: #93c2f7;
    --text-on-blue: #ffffff;
  }
  * { box-sizing: border-box; margin: 0; padding: 0; }
  html, body {
    width: 1200px; height: 900px; overflow: hidden;
    background: var(--page-bg);
    font-family: "Arimo", Arial, sans-serif;
  }
  .canvas { position: relative; width: 1200px; height: 900px; }

  .card {
    position: absolute;
    border-radius: 14px;
    box-shadow: 0 8px 24px rgba(35, 40, 55, 0.16);
    overflow: hidden;
  }

  /* Front side */
  .card-front {
    left: 178px; top: 74px; width: 588px; height: 364px;
    background: linear-gradient(160deg, var(--grad-start) 0%, #4c8ae8 45%, var(--grad-end) 100%);
    color: var(--text-on-blue);
    text-align: right;
    padding: 50px 36px 0 0;
  }
  .person-name { font-size: 22px; font-weight: 700; letter-spacing: 0.3px; }
  .credentials { font-size: 15px; margin-top: 6px; }
  .contact-list { list-style: none; margin-top: 13px; }
  .contact-list li {
    font-size: 17px; line-height: 24.5px;
    display: flex; justify-content: flex-end; align-items: center; gap: 6px;
  }
  .contact-icon { width: 15px; height: 15px; flex: none; }
  .service-list { list-style: none; margin-top: 46px; }
  .service-list li {
    font-size: 15.5px; line-height: 19px;
    display: flex; justify-content: flex-end; align-items: center; gap: 6px;
  }
  .service-marker { width: 10px; height: 10px; background: var(--text-on-blue); flex: none; }

  /* Back side */
  .card-back {
    left: 388px; top: 505px; width: 567px; height: 352px;
    background: var(--card-white);
    text-align: center;
  }
  .brand-name {
    position: absolute; left: 0; right: 0; top: 136px;
    font-size: 44px; font-weight: 700; letter-spacing: 6px;
    color: var(--brand-dark);
  }
  .brand-tagline {
    position: absolute; left: 0; right: 0; top: 184px;
    font-size: 14px; font-weight: 700; letter-spacing: 3px;
    color: var(--brand-dark);
  }
  .divider {
    position: absolute; left: 106px; top: 279px; width: 355px; height: 0;
    border-top: 3px solid var(--brand-blue);
  }
  .call-to-action {
    position: absolute; left: 0; right: 0; top: 296px;
    font-size: 15px; font-weight: 700; color: var(--blue-deep);
  }
</style>
</head>
<body>
<main class="canvas">
  <section class="card card-front" aria-label="Business card front">
    <h1 class="person-name">DEREK FULHAM</h1>
    <p class="credentials">MSc, CAT(C), RMT, CSCS, Pn2</p>
    <ul class="contact-list">
      <li>derek@vantrelo.com
        <svg class="contact-icon" viewBox="0 0 16 16" aria-hidden="true">
          <rect x="1" y="3" width="14" height="10" rx="1" fill="#fff"/>
          <path d="M1.5 3.8 8 9l6.5-5.2" fill="none" stroke="#5a94e8" stroke-width="1.3"/>
        </svg>
      </li>
      <li>www.vantrelo.com
        <svg class="contact-icon" viewBox="0 0 16 16" aria-hidden="true">
          <circle cx="8" cy="8" r="7" fill="#fff"/>
          <g fill="none" stroke="#5a94e8" stroke-width="1">
            <ellipse cx="8" cy="8" rx="3" ry="6.5"/>
            <path d="M1.5 8h13M2.5 5h11M2.5 11h11"/>
          </g>
        </svg>
      </li>
      <li>@derek_fulham
        <svg class="contact-icon" viewBox="0 0 16 16" aria-hidden="true">
          <rect x="1" y="1" width="14" height="14" rx="2" fill="#fff"/>
        </svg>
      </li>
    </ul>
    <ul class="service-list">
      <li>Personal Training <span class="service-marker"></span></li>
      <li>Golf Fitness <span class="service-marker"></span></li>
      <li>Injury Rehab <span class="service-marker"></span></li>
      <li>Massage Therapy <span class="service-marker"></span></li>
      <li>Yoga <span class="service-marker"></span></li>
    </ul>
  </section>

  <section class="card card-back" aria-label="Business card back">
    <p class="brand-name">VANTRELO</p>
    <p class="brand-tagline">NUTRITION - FITNESS - HEALTH</p>
    <div class="divider" aria-hidden="true"></div>
    <p class="call-to-action">CONTACT US TO RECEIVE&nbsp; A FREE ASSESSMENT</p>
  </section>
</main>
</body>
</html>
```